TALVORE GROUP OF CLINICS

We need a medical & lab report file. The design should be healthcare related. Our current file design has been used for almost 10 years. We need something more fresh & up-to-date. We have attached the current file design.

Need extra days to review

```html
<!DOCTYPE html>
<html lang="en">
<head>
<meta charset="utf-8">
<title>Talvore Group of Clinics — Medical Report Folder</title>
<link href="https://fonts.googleapis.com/css2?family=Montserrat:wght@600;800&family=Open+Sans:wght@400;700&family=Cormorant+Garamond:ital,wght@1,600&display=swap" rel="stylesheet">
<style>
  :root{
    --blue:#1f6fc4;
    --blue-deep:#2a3f9e;
    --blue-bright:#1c8fe0;
    --sky:#8fd3f4;
    --navy:#2e3192;
    --gold:#f2b91e;
    --gold-light:#ffe27a;
    --paper:#f4f5f7;
    --ink:#3b3f48;
    --white:#ffffff;
    --photo-light:#eceef2;
    --photo-mid:#c9ced7;
    --photo-dark:#a9b0bc;
  }
  *{box-sizing:border-box;margin:0;padding:0}
  html,body{width:1200px;height:847px;overflow:hidden;background:#cfd2d6}
  .folder{position:relative;width:1200px;height:847px;display:flex}
  .panel{position:relative;width:600px;height:847px;overflow:hidden;background:var(--paper)}
  .panel svg.shapes{position:absolute;inset:0;width:600px;height:847px}
  .photo{position:absolute}

  /* inside panel: clinic directory */
  .directory-title{
    position:absolute;left:120px;top:52px;width:280px;height:34px;
    background:linear-gradient(var(--blue-bright),var(--blue-deep));
    transform:rotate(-8deg);
    box-shadow:0 4px 6px rgba(0,0,0,.35);
    color:var(--white);font:800 17px/34px "Montserrat",sans-serif;
    text-align:center;letter-spacing:.3px;
  }
  .clinic{
    position:absolute;width:238px;height:76px;padding:8px 10px;
    background:linear-gradient(180deg,#ffffff 0%,#e3e5e9 60%,#c9ccd2 100%);
    box-shadow:3px 5px 0 #1d2f7a, 0 6px 10px rgba(0,0,0,.35);
    text-align:center;color:var(--ink);
    font:400 7.4px/1.35 "Open Sans",sans-serif;
  }
  .clinic h3{font:700 8.6px/1.3 "Open Sans",sans-serif;color:var(--navy);text-transform:uppercase;margin-bottom:2px}

  /* cover panel */
  .brand{
    position:absolute;left:52px;top:70px;width:180px;text-align:center;
    color:var(--white);font:800 14px/1 "Montserrat",sans-serif;letter-spacing:.5px;
  }
  .brand .dot{display:block;width:34px;height:34px;border-radius:50%;background:var(--white);margin:0 auto 12px}
  .report-title{
    position:absolute;left:0;right:0;top:232px;text-align:center;
    font:800 44px/1 "Montserrat",sans-serif;color:var(--navy);
    text-shadow:2px 2px 0 #fff,-2px -2px 0 #fff,2px -2px 0 #fff,-2px 2px 0 #fff,3px 5px 6px rgba(0,0,0,.35);
  }
  .tagline{
    position:absolute;left:0;right:0;top:338px;text-align:center;
    font:italic 600 26px/1 "Cormorant Garamond",serif;color:var(--white);
    text-shadow:0 1px 2px rgba(0,60,120,.35);
  }
  .confidential{
    position:absolute;left:0;right:0;top:772px;text-align:center;
    font:600 22px/1 "Montserrat",sans-serif;color:var(--white);letter-spacing:.6px;
  }
</style>
</head>
<body>
<div class="folder">

  <!-- Inside left: clinic directory -->
  <section class="panel panel-directory">
    <div class="photo" role="img" aria-label="Soft greyscale photo of a doctor's hands holding a clipboard" style="left:0;top:470px;width:600px;height:377px;background:radial-gradient(ellipse 60% 55% at 42% 55%,var(--photo-dark) 0%,var(--photo-mid) 40%,var(--photo-light) 80%,#f4f5f7 100%)"></div>
    <svg class="shapes" viewBox="0 0 600 847" aria-hidden="true">
      <defs>
        <linearGradient id="dirBlue" x1="0" y1="0" x2="1" y2="1">
          <stop offset="0" stop-color="#1c8fe0"/>
          <stop offset=".55" stop-color="#1f6fc4"/>
          <stop offset="1" stop-color="#2a3f9e"/>
        </linearGradient>
        <linearGradient id="dirGold" x1="0" x2="1">
          <stop offset="0" stop-color="#f2b91e"/>
          <stop offset=".5" stop-color="#ffe27a"/>
          <stop offset="1" stop-color="#e0a412"/>
        </linearGradient>
      </defs>
      <path d="M0 22 L600 8 L600 470 L0 610 Z" fill="url(#dirBlue)"/>
      <path d="M0 22 L600 8 L600 60 C420 120 180 60 0 110 Z" fill="#3aa4ec" opacity=".35"/>
      <path d="M0 470 C200 430 420 330 600 250 L600 470 L0 610 Z" fill="#2a3f9e" opacity=".35"/>
      <path d="M0 610 L600 470" stroke="url(#dirGold)" stroke-width="6"/>
      <path d="M0 18 L600 4" stroke="url(#dirGold)" stroke-width="4"/>
      <path d="M600 8 L600 470" stroke="url(#dirGold)" stroke-width="4"/>
      <path d="M490 500 L600 474 L600 640 Z" fill="url(#dirBlue)" stroke="url(#dirGold)" stroke-width="5" stroke-linejoin="round"/>
      <g fill="#1c5fbf" opacity=".9">
        <path d="M282 150 L322 138 L322 174 L282 186 Z"/>
        <path d="M282 246 L322 234 L322 270 L282 282 Z"/>
        <path d="M282 342 L322 330 L322 366 L282 378 Z"/>
      </g>
      <rect x="0" y="836" width="600" height="11" fill="#2a3f9e"/>
    </svg>

    <div class="directory-title">TALVORE GROUP OF CLINICS</div>

    <div class="clinic" style="left:330px;top:96px">
      <h3>Klinik Talvore (Seroja)</h3>
      No. 22, Jalan Seroja 4, Taman Seroja,<br>40460 Shah Alam, Selangor.<br>Tel: +603-5550-2301 Fax: +603-5550-2302<br>Email: care@talvoreclinics.example
    </div>
    <div class="clinic" style="left:34px;top:140px">
      <h3>Pusat Perubatan Talvore</h3>
      Level 12, Orvel Tower, No.8, Jalan Cempaka Indah,<br>50470 Kuala Lumpur.<br>Tel: +603-5550-1201 Fax: +603-5550-1202<br>Email: care@talvoreclinics.example
    </div>
    <div class="clinic" style="left:330px;top:192px">
      <h3>Klinik Talvore (Tasik Permai)</h3>
      No. 45, Jalan Niaga Tasik 2,<br>71800 Bandar Tasik Permai, Negeri Sembilan.<br>Tel: +606-555-3401 Fax: +606-555-3402<br>Email: tasik@talvoreclinics.example
    </div>
    <div class="clinic" style="left:34px;top:236px">
      <h3>Klinik Talvore (Bayan Baru)</h3>
      Lot 7-1-2, Lebuh Merbah, Taman Merbah,<br>11950 Bayan Baru, Penang.<br>Tel: +604-555-4501 Fax: +604-555-4502<br>Email: bayan@talvoreclinics.example
    </div>
    <div class="clinic" style="left:330px;top:288px">
      <h3>Talvore Medical Clinic (Terminal B)</h3>
      Unit 3-14, Arrival Concourse, Terminal B,<br>64100 Sepang, Selangor.<br>Tel: +603-5550-5601 Fax: +603-5550-5602<br>Email: termb@talvoreclinics.example
    </div>
    <div class="clinic" style="left:34px;top:332px">
      <h3>Talvore Medical Clinic (Terminal A)</h3>
      Lot A-09, Arrival Hall, Terminal A,<br>64100 Sepang, Selangor.<br>Tel: +603-5550-6701 Fax: +603-5550-6702<br>Email: terma@talvoreclinics.example
    </div>
    <div class="clinic" style="left:160px;top:426px">
      <h3>Talvore Medical Clinic (Northport)</h3>
      Level 1, Passenger Hall, Northport Air Terminal,<br>11960 Bayan Baru, Penang.<br>Tel: +604-555-7801 Fax: +604-555-7802<br>Email: northport@talvoreclinics.example
    </div>
  </section>

  <!-- Front cover -->
  <section class="panel panel-cover" style="background:var(--white)">
    <div class="photo" role="img" aria-label="Soft greyscale photo of a doctor with stethoscope offering an open hand" style="left:0;top:200px;width:600px;height:500px;background:radial-gradient(ellipse 45% 40% at 30% 70%,var(--photo-mid) 0%,transparent 100%),radial-gradient(ellipse 70% 60% at 60% 35%,var(--photo-dark) 0%,var(--photo-mid) 35%,var(--photo-light) 75%,#f4f5f7 100%)"></div>
    <svg class="shapes" viewBox="0 0 600 847" aria-hidden="true">
      <defs>
        <linearGradient id="coverBlue" x1="0" y1="0" x2="1" y2="0">
          <stop offset="0" stop-color="#1c8fe0"/>
          <stop offset=".6" stop-color="#1f6fc4"/>
          <stop offset="1" stop-color="#2a3f9e"/>
        </linearGradient>
        <linearGradient id="coverGold" x1="0" x2="1">
          <stop offset="0" stop-color="#e0a412"/>
          <stop offset=".5" stop-color="#ffe27a"/>
          <stop offset="1" stop-color="#f2b91e"/>
        </linearGradient>
        <linearGradient id="bottomBlue" x1="0" y1="0" x2="1" y2="1">
          <stop offset="0" stop-color="#2f5fc0"/>
          <stop offset="1" stop-color="#2a3f9e"/>
        </linearGradient>
      </defs>
      <path d="M0 34 C200 44 420 36 600 26" stroke="url(#coverGold)" stroke-width="5" fill="none"/>
      <path d="M0 44 C200 54 420 46 600 36 L600 150 C420 175 220 195 0 210 Z" fill="url(#coverBlue)"/>
      <circle cx="145" cy="112" r="118" fill="#8fd3f4" opacity=".35"/>
      <path d="M0 218 C220 203 420 182 600 156" stroke="url(#coverGold)" stroke-width="7" fill="none"/>
      <path d="M0 330 L600 312 L600 362 L0 384 Z" fill="#8fd3f4" opacity=".85"/>
      <path d="M0 700 C220 700 420 640 600 560 L600 847 L0 847 Z" fill="url(#bottomBlue)"/>
      <path d="M0 690 C240 690 430 630 600 540" stroke="url(#coverGold)" stroke-width="8" fill="none"/>
      <path d="M0 720 C200 712 330 690 450 640 C330 700 200 735 0 745 Z" fill="#1c8fe0"/>
      <path d="M0 710 C200 705 340 680 460 630" stroke="url(#coverGold)" stroke-width="4" fill="none"/>
      <path d="M380 640 C460 615 540 575 600 530" stroke="url(#coverGold)" stroke-width="3" fill="none"/>
      <rect x="0" y="836" width="600" height="11" fill="#2a3f9e"/>
    </svg>

    <div class="brand"><span class="dot"></span>TALVORE GROUP</div>
    <h1 class="report-title">MEDICAL REPORT</h1>
    <p class="tagline">“Your Healthcare Partner”</p>
    <p class="confidential">PRIVATE &amp; CONFIDENTIAL</p>
  </section>

</div>
</body>
</html>
```